Website Design for Wheels for Servicemen.org - Donated Cars to Disabled Vets

Need a Wordpress website. The coding now, esp. the CDONT coding is not supported by many hosting sites. Looking for a landing page to generate leads.

Logo Text

look at current one for ideas

Coding

Coded - Design and coding required

Number of Pages Required

1 page

Requirements
Must have
• look at current website at www.wheelsforservicemen.org
Nice to have
• look at this site: http://givevehicletoservicemen.org

```html
<!DOCTYPE html>
<html lang="en">
<head>
<meta charset="utf-8">
<title>Wheels for Servicemen — Donate Your Car</title>
<link href="https://fonts.googleapis.com/css2?family=Montserrat:wght@400;600;700&family=Open+Sans:wght@400;600;700&display=swap" rel="stylesheet">
<style>
:root{
  --blue:#1f56a8;
  --blue-deep:#1a4a94;
  --red:#d11f2f;
  --ink:#222;
  --muted:#6b6b6b;
  --line:#dedede;
  --footer:#f5f5f5;
  --white:#fff;
}
*{box-sizing:border-box;margin:0;padding:0}
html,body{width:1200px;height:2390px;overflow:hidden;background:var(--white)}
body{font-family:"Open Sans",sans-serif;color:var(--ink);position:relative}
.wrap{width:936px;margin:0 auto;position:relative}
h1,h2,h3,.brand,.nav a{font-family:"Montserrat",sans-serif}

/* header */
.topbar{height:113px;background:var(--blue);border-bottom:3px solid var(--red)}
.topbar .wrap{height:110px;display:flex;align-items:center;justify-content:space-between}
.brand{display:flex;align-items:center;gap:12px;color:var(--white);font-size:21px;font-weight:600}
.brand-mark{width:30px;height:30px;background:var(--red);border-radius:50%}
.hotline{display:flex;align-items:center;gap:14px;color:var(--white);text-align:right}
.hotline small{display:block;font-size:12px}
.hotline strong{display:block;font-family:"Montserrat",sans-serif;font-size:18px;margin-top:4px}
.operator{width:60px;height:60px;border-radius:50%;border:3px solid var(--white);background:linear-gradient(#e9d7c8,#b89a86)}

.nav{height:53px;background:var(--white)}
.nav .wrap{height:53px;display:flex;justify-content:space-between;align-items:center}
.nav a{font-size:11px;color:var(--ink);text-decoration:none;text-transform:uppercase;height:53px;line-height:53px;padding:0 26px}
.nav a.active{background:var(--red);color:var(--white);padding:0 48px}

/* hero */
.hero{height:508px;position:relative;background:linear-gradient(120deg,#6f7d5e,#8c8f74 45%,#5f6e4e)}
.hero-arrow{position:absolute;top:402px;width:36px;height:36px;border-radius:50%;background:rgba(255,255,255,.55)}
.hero-arrow.prev{left:72px}.hero-arrow.next{right:76px}
.hero-arrow svg{width:36px;height:36px}
.hero-caption{position:absolute;left:147px;top:252px;width:366px;height:116px;background:rgba(20,30,45,.55);color:var(--white);text-align:center;padding-top:18px}
.hero-caption p{font-family:"Montserrat",sans-serif;font-size:18px;letter-spacing:.5px}
.hero-caption h1{font-size:44px;font-weight:700;line-height:1.1;margin-top:4px}

.donate-form{position:absolute;left:711px;top:0;width:357px;height:508px;background:rgba(235,238,243,.9);padding:22px 18px 0}
.form-head{display:flex;align-items:center;gap:22px}
.form-car{width:108px;height:62px;border-radius:30px 30px 10px 10px;background:linear-gradient(#e8e8e8,#a9a9a9)}
.form-head h2{font-size:21px;font-weight:400;line-height:1.3;text-align:center}
.form-phone{text-align:center;color:var(--red);font-family:"Montserrat",sans-serif;font-weight:700;font-size:24px;margin:16px 0 12px}
.form-note{border-top:1px solid #aaa;margin:0 18px;padding-top:14px;text-align:center;font-size:12.5px;color:#333}
.fields{display:grid;grid-template-columns:1fr 1fr;gap:16px 6px;margin-top:12px}
.fields label{font-size:11.5px;color:#444;display:block;margin-bottom:5px}
.fields span{display:block;height:29px;background:var(--white);border:1px solid #ccc;font-size:9px;color:#999;text-align:center;line-height:27px}
.submit{display:block;margin:15px auto 0;width:222px;height:37px;background:var(--red);color:var(--white);font-family:"Montserrat",sans-serif;font-size:12px;font-weight:700;border:0}

/* how it works */
.how{height:380px;padding-top:66px;text-align:center}
.section-title{font-size:26px;font-weight:600;letter-spacing:.3px}
.how .lead{width:700px;margin:14px auto 0;font-size:11px;line-height:1.9;color:var(--muted)}
.steps{display:flex;gap:0;margin-top:50px;text-align:left}
.step{width:330px;display:flex;gap:22px}
.step-icon{width:80px;height:80px;flex:none;border:2px solid var(--blue);border-radius:50%;display:flex;align-items:center;justify-content:center}
.step-icon svg{width:46px;height:46px}
.step h3{font-size:13px;font-weight:600;margin-top:6px}
.step p{font-size:11.5px;line-height:1.85;color:var(--muted);margin-top:8px;width:175px}
.step a{font-size:9.5px;color:var(--red);font-weight:700;text-decoration:none;text-transform:uppercase;display:block;margin-top:8px}

/* why */
.why{height:510px;background:linear-gradient(100deg,#2359ab 0%,#2c62b2 55%,#3a6bb0 80%,#2f5fa8 100%);color:var(--white);padding-top:66px}
.why .section-title{font-size:24px;font-weight:500}
.why ul{list-style:none;margin-top:30px}
.why li{display:flex;align-items:center;gap:14px;font-size:11.5px;height:48px}
.why li svg{width:27px;height:27px;flex:none}
.why li b{font-weight:700}

/* program */
.program{height:677px;padding-top:80px}
.program .section-title{text-align:center}
.cards{display:grid;grid-template-columns:450px 450px;gap:36px;margin-top:40px}
.card{height:204px;border:1px solid var(--line);padding:24px 30px 0;box-shadow:0 1px 2px rgba(0,0,0,.04)}
.card-head{display:flex;align-items:center;gap:26px;height:70px}
.card-head svg{width:84px;height:66px;flex:none}
.map-fill{width:100px;height:62px;flex:none;background:var(--red);border-radius:10px 18px 24px 12px}
.card h3{font-size:14px;font-weight:500;line-height:1.9}
.card p{font-size:11px;line-height:2.1;color:var(--muted);margin-top:12px}

/* footer */
.footer{height:149px;background:var(--footer);text-align:center;padding-top:34px}
.social{display:flex;justify-content:center;gap:5px}
.social span{width:27px;height:27px;border-radius:50%}
.footer nav{margin-top:14px;font-size:11.5px;color:#444}
.footer nav i{font-style:normal;margin:0 18px}
.footer small{display:block;margin-top:8px;font-size:11px;color:#555}
</style>
</head>
<body>

<header class="topbar">
  <div class="wrap">
    <div class="brand"><span class="brand-mark"></span>Wheels for Servicemen</div>
    <div class="hotline">
      <div><small>Live Operators Available 7 Days a Week</small><strong>Call 1-800-555-0142</strong></div>
      <div class="operator" role="img" aria-label="Portrait of a phone operator with headset"></div>
    </div>
  </div>
</header>

<nav class="nav">
  <div class="wrap">
    <a class="active" href="#">Home</a><a href="#">About Us</a><a href="#">Services</a><a href="#">Donation Program</a><a href="#">Careers</a><a href="#">Blog</a><a href="#">Contact</a>
  </div>
</nav>

<section class="hero" role="img" aria-label="Photo of a soldier in uniform holding his laughing son, with an American flag, in a garden">
  <span class="hero-arrow prev"><svg viewBox="0 0 36 36"><path d="M21 11l-7 7 7 7" fill="none" stroke="#555" stroke-width="3"/></svg></span>
  <span class="hero-arrow next"><svg viewBox="0 0 36 36"><path d="M15 11l7 7-7 7" fill="none" stroke="#555" stroke-width="3"/></svg></span>
  <div class="hero-caption"><p>DONATE YOUR CAR</p><h1>TO VETERANS</h1></div>

  <form class="donate-form">
    <div class="form-head">
      <div class="form-car" role="img" aria-label="Illustration of a silver sedan"></div>
      <h2>Call Today to<br>Donate</h2>
    </div>
    <div class="form-phone">1-800-555-0142</div>
    <p class="form-note">Or Fill out the form below to instantly donate online</p>
    <div class="fields">
      <div><label>Name*</label><span></span></div>
      <div><label>E-mail*</label><span></span></div>
      <div><label>Phone Number*</label><span></span></div>
      <div><label>Cell Phone*</label><span></span></div>
      <div><label>Address*</label><span></span></div>
      <div><label>City*</label><span></span></div>
      <div><label>State*</label><span>- Selected -</span></div>
      <div><label>Zip Code*</label><span></span></div>
    </div>
    <button class="submit" type="button">CLICK TO DONATE YOUR CAR</button>
  </form>
</section>

<section class="how">
  <div class="wrap">
    <h2 class="section-title">HOW IT WORKS</h2>
    <p class="lead">Sed ut perspiciatis unde omnis iste natus error sit voluptatem accusantium doloremque laudantium, totam rem aperiam, eaque ipsa quae ab illo inventore veritatis et quasi architecto beatae vitae dicta sunt explicabo...</p>
    <div class="steps">
      <div class="step">
        <div class="step-icon"><svg viewBox="0 0 46 46"><path d="M6 16c0-5 5-8 17-8s17 3 17 8v3h-8v-4H14v4H6z" fill="#1f56a8"/><rect x="10" y="22" width="26" height="16" rx="3" fill="#1f56a8"/><circle cx="23" cy="30" r="5" fill="#fff"/></svg></div>
        <div><h3>CALL US</h3><p>Nemo enim voluptatem quia voluptas sit aspernatur aut odit aut fugit,ratione...</p><a href="#">View details &gt;&gt;</a></div>
      </div>
      <div class="step">
        <div class="step-icon"><svg viewBox="0 0 46 46"><rect x="2" y="14" width="22" height="16" rx="2" fill="#1f56a8"/><path d="M24 18h8l6 7v5H24z" fill="#1f56a8"/><path d="M28 20h4l4 5h-8z" fill="#fff"/><circle cx="10" cy="32" r="4" fill="#1f56a8" stroke="#fff" stroke-width="2"/><circle cx="32" cy="32" r="4" fill="#1f56a8" stroke="#fff" stroke-width="2"/><path d="M38 28l6-6" stroke="#1f56a8" stroke-width="2"/></svg></div>
        <div><h3>WE TOW IT</h3><p>Nemo enim voluptatem quia voluptas sit aspernatur aut odit aut fugit,ratione...</p><a href="#">View details &gt;&gt;</a></div>
      </div>
      <div class="step">
        <div class="step-icon"><svg viewBox="0 0 46 46"><rect x="8" y="8" width="26" height="32" rx="2" fill="#1f56a8"/><path d="M13 16h16M13 22h12M13 28h8" stroke="#fff" stroke-width="2.5"/><path d="M24 34l14-14 4 4-14 14h-4z" fill="#1f56a8" stroke="#fff" stroke-width="2"/></svg></div>
        <div><h3>TAX WRITE OFF</h3><p>Nemo enim voluptatem quia voluptas sit aspernatur aut odit aut fugit,ratione...</p><a href="#">View details &gt;&gt;</a></div>
      </div>
    </div>
  </div>
</section>

<section class="why" role="img" aria-label="Blue-tinted photo of a smiling military family in front of a white picket fence">
  <div class="wrap">
    <h2 class="section-title">WHY DONATE YOUR CAR TO US?</h2>
    <ul>
      <li><svg viewBox="0 0 27 27"><circle cx="13.5" cy="13.5" r="12.5" fill="none" stroke="#fff" stroke-width="1.5"/><path d="M8 14l4 4 7-8" fill="none" stroke="#fff" stroke-width="2"/></svg><span><b>IRS 501(c)3 Approved:</b> Free 24/7 Pickup with No DMV Hassles.</span></li>
      <li><svg viewBox="0 0 27 27"><circle cx="13.5" cy="13.5" r="12.5" fill="none" stroke="#fff" stroke-width="1.5"/><path d="M8 14l4 4 7-8" fill="none" stroke="#fff" stroke-width="2"/></svg><span><b>Free Local Towing to You:</b> We will pick up your car donation, running or not, when it's most convenient, at home or work.</span></li>
      <li><svg viewBox="0 0 27 27"><circle cx="13.5" cy="13.5" r="12.5" fill="none" stroke="#fff" stroke-width="1.5"/><path d="M8 14l4 4 7-8" fill="none" stroke="#fff" stroke-width="2"/></svg><span><b>All Cars Accepted:</b> We take your car regardless of its condition or registration status.</span></li>
      <li><svg viewBox="0 0 27 27"><circle cx="13.5" cy="13.5" r="12.5" fill="none" stroke="#fff" stroke-width="1.5"/><path d="M8 14l4 4 7-8" fill="none" stroke="#fff" stroke-width="2"/></svg><span><b>Income Tax Deduction:</b> We issue you an IRS tax receipt &amp; offer the largest resale network to get you the highest tax write-off possible.</span></li>
      <li><svg viewBox="0 0 27 27"><circle cx="13.5" cy="13.5" r="12.5" fill="none" stroke="#fff" stroke-width="1.5"/><path d="M8 14l4 4 7-8" fill="none" stroke="#fff" stroke-width="2"/></svg><span><b>No Paperwork Hassles:</b> We take any car and handle everything: DMV, Smog and IRS paperwork.</span></li>
      <li><svg viewBox="0 0 27 27"><circle cx="13.5" cy="13.5" r="12.5" fill="none" stroke="#fff" stroke-width="1.5"/><path d="M8 14l4 4 7-8" fill="none" stroke="#fff" stroke-width="2"/></svg><span><b>Car donations help fund programs:</b> And benefit Servicemen Support Trust. An IRS 501(c)3 nonprofit organization.</span></li>
      <li><svg viewBox="0 0 27 27"><circle cx="13.5" cy="13.5" r="12.5" fill="none" stroke="#fff" stroke-width="1.5"/><path d="M8 14l4 4 7-8" fill="none" stroke="#fff" stroke-width="2"/></svg><span><b>Schedule a Free Pickup:</b> Complete the form and a representative will call you to arrange a convenient time to pickup your car.</span></li>
    </ul>
  </div>
</section>

<section class="program">
  <div class="wrap">
    <h2 class="section-title">CAR DONATION PROGRAM</h2>
    <div class="cards">
      <article class="card">
        <div class="card-head"><div class="map-fill" role="img" aria-label="Red map of the United States"></div><h3>Donations Accepted<br>Nationwide</h3></div>
        <p>Perspiciatis unde omnis iste natus error sit voluptatem laudantium, totam rem aperiam, eaque ipsa quae ab illo inventore veritatis perspiciatis unde omnis iste natus error sit voluptatem accusantium...</p>
      </article>
      <article class="card">
        <div class="card-head"><svg viewBox="0 0 84 66"><path d="M14 30l8-16h40l8 16" fill="none" stroke="#d11f2f" stroke-width="5"/><rect x="8" y="30" width="68" height="20" rx="5" fill="#d11f2f"/><circle cx="22" cy="40" r="4" fill="#fff"/><circle cx="62" cy="40" r="4" fill="#fff"/><rect x="12" y="50" width="12" height="8" fill="#d11f2f"/><rect x="60" y="50" width="12" height="8" fill="#d11f2f"/></svg><h3>All Vechile Types<br>Welcome</h3></div>
        <p>Perspiciatis unde omnis iste natus error sit voluptatem laudantium, totam rem aperiam, eaque ipsa quae ab illo inventore veritatis perspiciatis unde omnis iste natus error sit voluptatem accusantium...</p>
      </article>
      <article class="card">
        <div class="card-head"><svg viewBox="0 0 84 66"><path d="M4 2h24l12 12v42H4z" fill="#d11f2f"/><path d="M11 24h20M11 32h16M11 40h12" stroke="#fff" stroke-width="3"/><path d="M30 52l6 6 12-14" fill="none" stroke="#d11f2f" stroke-width="5"/></svg><h3>Tax Deductible</h3></div>
        <p>Perspiciatis unde omnis iste natus error sit voluptatem laudantium, totam rem aperiam, eaque ipsa quae ab illo inventore veritatis perspiciatis unde omnis iste natus error sit voluptatem accusantium...</p>
      </article>
      <article class="card">
        <div class="card-head"><svg viewBox="0 0 84 66"><path d="M30 14h22l10 18v18H30z" fill="none" stroke="#d11f2f" stroke-width="5"/><rect x="4" y="34" width="28" height="14" fill="#d11f2f"/><path d="M8 34l14-24M18 4v14" stroke="#d11f2f" stroke-width="4"/><circle cx="16" cy="52" r="7" fill="#fff" stroke="#d11f2f" stroke-width="4"/><circle cx="52" cy="52" r="7" fill="#fff" stroke="#d11f2f" stroke-width="4"/></svg><h3>Towing is Free</h3></div>
        <p>Perspiciatis unde omnis iste natus error sit voluptatem laudantium, totam rem aperiam, eaque ipsa quae ab illo inventore veritatis perspiciatis unde omnis iste natus error sit voluptatem accusantium...</p>
      </article>
    </div>
  </div>
</section>

<footer class="footer">
  <div class="social"><span style="background:#2a3f7a"></span><span style="background:#2fa3d9"></span><span style="background:#d9342b"></span><span style="background:#9b7a5a"></span></div>
  <nav>Home<i>/</i>About Us<i>/</i>Services<i>/</i>Donation Program<i>/</i>Careers<i>/</i>Blog<i>/</i>Contact</nav>
  <small>Copyrights © 2016 . wheelsforservicemen | Allrights Reserved.</small>
</footer>

</body>
</html>
```